Business Card Design Project

This is the first time we use our new logo. We need a business card that we can use both on our institutional corporate relationships and also that works for our staff that deals with consumers directly.

VELUNDA is a new company dedicated to empower consumers and to provide them with the best choices for specialized health care using the latest telemedicine technology (medicine at a distance via videoconference).

We want to print this cards in high quality materials and process. We will like designs that allow us to use UV spot varnish and other techniques that will differentiate us.

We are including Two different versions of Color logos. In addition we are including white over black background logos. Those can be used replacing the black for a color.

Please note this is the first time we will be creating any corporate materials with our new logo and colors.

Target Market(s)

34+ consumers of medium high and high socioeconomic levels.

Industry/Entity Type

Health

Requirements
Must have
• Our logo on its original colors
Should not have
• Any other graphical element or design that is not our logo

```html
<!DOCTYPE html>
<html lang="en">
<head>
<meta charset="utf-8">
<title>VELUNDA Business Card</title>
<link href="https://fonts.googleapis.com/css2?family=Montserrat:wght@700&family=Arimo:wght@400;700&display=swap" rel="stylesheet">
<style>
  :root {
    --page-bg: #e9e6e2;
    --card-white: #ffffff;
    --brand-navy: #1f5a8c;
    --brand-sky: #5ab4e0;
    --brand-teal: #0aa79f;
    --ink: #222222;
    --icon: #3d7fb3;
  }
  html, body {
    margin: 0;
    padding: 0;
    width: 1200px;
    height: 872px;
    overflow: hidden;
    background: var(--page-bg);
  }
  .canvas {
    position: relative;
    width: 1200px;
    height: 872px;
  }
  .card {
    position: absolute;
    top: 106px;
    width: 380px;
    height: 660px;
    box-shadow: 0 6px 22px rgba(0,0,0,0.18);
    overflow: hidden;
  }
  .card-front {
    left: 170px;
    background: var(--card-white);
  }
  .card-back {
    left: 650px;
    background: var(--brand-teal);
  }
  .brand {
    position: absolute;
    left: 0;
    right: 0;
    top: 150px;
    display: flex;
    align-items: center;
    justify-content: center;
    gap: 14px;
  }
  .brand-dot {
    width: 26px;
    height: 26px;
    border-radius: 50%;
    background: var(--brand-teal);
  }
  .brand-name {
    font-family: "Montserrat", sans-serif;
    font-weight: 700;
    font-size: 46px;
    letter-spacing: 3px;
    color: var(--brand-navy);
  }
  .person {
    position: absolute;
    top: 290px;
    left: 0;
    right: 0;
    text-align: center;
    font-family: "Arimo", sans-serif;
    font-size: 29px;
  }
  .person-name {
    font-weight: 700;
    color: var(--brand-navy);
  }
  .person-title {
    color: var(--brand-sky);
    font-size: 24px;
  }
  .contacts {
    position: absolute;
    top: 360px;
    left: 78px;
    margin: 0;
    padding: 0;
    list-style: none;
    font-family: "Arimo", sans-serif;
    font-size: 23px;
    color: var(--ink);
  }
  .contacts li {
    display: flex;
    align-items: center;
    gap: 12px;
    height: 38px;
  }
  .contacts svg {
    width: 20px;
    height: 20px;
    flex: none;
  }
  .swoosh {
    position: absolute;
    left: 0;
    top: 500px;
    width: 380px;
    height: 90px;
  }
  .address {
    position: absolute;
    top: 560px;
    left: 0;
    right: 0;
    text-align: center;
    font-family: "Arimo", sans-serif;
    font-size: 23px;
    line-height: 1.3;
    color: var(--ink);
  }
  .back-name {
    position: absolute;
    top: 270px;
    left: 0;
    right: 0;
    text-align: center;
    font-family: "Montserrat", sans-serif;
    font-weight: 700;
    font-size: 46px;
    letter-spacing: 3px;
    color: var(--card-white);
  }
  .back-web {
    position: absolute;
    bottom: 90px;
    left: 0;
    right: 0;
    text-align: center;
    font-family: "Arimo", sans-serif;
    font-size: 20px;
    letter-spacing: 4px;
    color: var(--card-white);
  }
</style>
</head>
<body>
<main class="canvas">
  <section class="card card-front" aria-label="Card front">
    <div class="brand">
      <span class="brand-dot"></span>
      <span class="brand-name">VELUNDA</span>
    </div>
    <p class="person"><span class="person-name">Your Name,</span> <span class="person-title">Title</span></p>
    <ul class="contacts">
      <li>
        <svg viewBox="0 0 20 20"><circle cx="10" cy="10" r="8.5" fill="none" stroke="var(--icon)" stroke-width="2"/><path d="M7 5.5c-1 1-1 3 .5 5.5s3.5 4 5 4l1.5-1.5-2-2-1.2.8c-1-.5-2-1.7-2.4-2.8l.9-1.1-1.6-2.4z" fill="var(--icon)"/></svg>
        <span>555-010-2040</span>
      </li>
      <li>
        <svg viewBox="0 0 20 20"><circle cx="10" cy="10" r="8.5" fill="none" stroke="var(--icon)" stroke-width="2"/><path d="M7 5.5c-1 1-1 3 .5 5.5s3.5 4 5 4l1.5-1.5-2-2-1.2.8c-1-.5-2-1.7-2.4-2.8l.9-1.1-1.6-2.4z" fill="var(--icon)"/></svg>
        <span>555-010-2040</span>
      </li>
      <li>
        <svg viewBox="0 0 20 20"><rect x="2" y="5" width="16" height="11" rx="1" fill="var(--icon)"/><path d="M2.5 5.5 10 11l7.5-5.5" fill="none" stroke="#fff" stroke-width="1.5"/></svg>
        <span>name@velunda.com</span>
      </li>
      <li>
        <svg viewBox="0 0 20 20"><circle cx="10" cy="10" r="8" fill="none" stroke="var(--icon)" stroke-width="1.8"/><ellipse cx="10" cy="10" rx="3.5" ry="8" fill="none" stroke="var(--icon)" stroke-width="1.4"/><path d="M2 10h16M3.5 6h13M3.5 14h13" stroke="var(--icon)" stroke-width="1.2"/></svg>
        <span>www.velunda.com</span>
      </li>
    </ul>
    <svg class="swoosh" viewBox="0 0 380 90" aria-hidden="true">
      <path d="M0 86 C90 20 250 0 380 18 C250 12 100 35 0 90 Z" fill="var(--brand-sky)"/>
    </svg>
    <p class="address">Street Name, City Name<br>State, City Zip Code</p>
  </section>

  <section class="card card-back" aria-label="Card back">
    <p class="back-name">VELUNDA</p>
    <p class="back-web">velunda.com</p>
  </section>
</main>
</body>
</html>
```